Mira Bloom Fitness Coaching Project

I am a personal trainer based in London. My services include one-on-one PT sessions, bootcamps.
I would like the design to be minimalistic. With light colours: white, pink, purple.
I specialise in weight loss, flexibility, mobility.

Tessa Brogan
Personal Trainer
Email: tessa.brogan@quellmail.com
tel: 07700218493
Instagram: Mira Bloom

Target Market(s)

adults, mostly females (age 18-50).

Industry/Entity Type

Fitness

Contact Information for Business Card

Tessa Brogan
Personal Trainer
tel: 07700218493
Instagram: Mira Bloom

Font styles to use
Serif

Colors
eea4c8
fbd4d5
fdf9cf
cfeae6
cee9f5

Requirements
Nice to have
• minimalistic style
• easy to read and remember

```html
<!DOCTYPE html>
<html lang="en">
<head>
<meta charset="utf-8">
<title>Mira Bloom Fitness Coaching – Business Card</title>
<link rel="stylesheet" href="https://fonts.googleapis.com/css2?family=Cinzel:wght@500&family=Open+Sans:wght@400;700&display=swap">
<style>
  :root {
    --page-bg: #ecebe8;
    --card-front: #d4ece8;
    --ink: #1d1d1d;
    --ink-soft: #2b2b2b;
    --band-dark: #1f3b40;
    --wall-teal: #3cc4cf;
    --wall-pink: #e21a72;
    --wall-blue: #2a57b5;
    --photo-ring: #1c2a2a;
    --photo-warm: #8a5a3a;
    --photo-light: #d9c7a6;
    --white: #ffffff;
  }
  * { box-sizing: border-box; margin: 0; padding: 0; }
  html, body { width: 1200px; height: 900px; overflow: hidden; }
  body {
    background: var(--page-bg);
    font-family: "Open Sans", Arial, sans-serif;
    position: relative;
  }
  .card {
    position: absolute;
    width: 560px;
    height: 320px;
    left: 320px;
    border-radius: 4px;
    overflow: hidden;
    box-shadow: 0 6px 18px rgba(0,0,0,0.18);
  }
  /* back side */
  .card--back { top: 95px; background: var(--band-dark); }
  .back-photo {
    position: absolute; inset: 0 0 70px 0;
    background:
      linear-gradient(180deg, var(--wall-pink) 0%, var(--wall-pink) 20%, var(--wall-teal) 24%, var(--wall-teal) 68%, var(--band-dark) 78%);
  }
  .specialties {
    position: absolute; left: 0; right: 0; bottom: 20px;
    display: flex; justify-content: center; gap: 14px;
    color: var(--white); font-size: 15px; list-style: none;
  }
  .specialties li::before {
    content: ""; display: inline-block; width: 7px; height: 7px;
    border-radius: 50%; background: var(--white);
    margin-right: 8px; vertical-align: middle;
  }
  /* front side */
  .card--front { top: 485px; background: var(--card-front); }
  .brand {
    position: absolute; left: 48px; top: 62px; width: 270px;
    display: flex; flex-direction: column; align-items: center; gap: 12px;
  }
  .brand-dot {
    width: 50px; height: 50px; border-radius: 50%;
    border: 3px solid var(--ink);
  }
  .brand-name {
    font-family: "Cinzel", Georgia, serif; font-weight: 500;
    font-size: 20px; color: var(--ink); text-align: center; line-height: 1.25;
  }
  .person { position: absolute; left: 60px; top: 200px; color: var(--ink); }
  .person-name { font-size: 21px; font-weight: 700; letter-spacing: 0.3px; line-height: 1.1; }
  .person-role { font-size: 15px; color: var(--ink-soft); margin-bottom: 12px; }
  .contact { list-style: none; font-size: 16px; color: var(--ink-soft); }
  .contact li { display: flex; align-items: center; gap: 8px; line-height: 1.6; }
  .contact svg { width: 14px; height: 14px; fill: var(--ink); flex: none; }
  .portrait {
    position: absolute; right: 24px; top: 24px;
    width: 232px; height: 232px; border-radius: 50%;
    border: 4px solid var(--photo-ring);
    background: radial-gradient(circle at 45% 40%, var(--photo-light) 0%, var(--photo-warm) 55%, var(--photo-ring) 100%);
  }
</style>
</head>
<body>
  <section class="card card--back">
    <div class="back-photo" role="img" aria-label="Photo of a trainer mid-jump in front of a painted pink, teal and dark mural wall"></div>
    <ul class="specialties">
      <li>Weight Loss</li>
      <li>Flexibility</li>
      <li>Mobility</li>
    </ul>
  </section>

  <section class="card card--front">
    <div class="brand">
      <span class="brand-dot"></span>
      <p class="brand-name">Mira Bloom Fitness<br>Coaching Project</p>
    </div>
    <div class="person">
      <h1 class="person-name">TESSA BROGAN</h1>
      <p class="person-role">Personal Trainer</p>
      <ul class="contact">
        <li>
          <svg viewBox="0 0 24 24" aria-hidden="true"><path d="M6.6 10.8a15.1 15.1 0 0 0 6.6 6.6l2.2-2.2a1 1 0 0 1 1-.25 11.4 11.4 0 0 0 3.6.57 1 1 0 0 1 1 1V20a1 1 0 0 1-1 1A17 17 0 0 1 3 4a1 1 0 0 1 1-1h3.5a1 1 0 0 1 1 1c0 1.25.2 2.45.57 3.57a1 1 0 0 1-.25 1z"/></svg>
          07700218493
        </li>
        <li>
          <svg viewBox="0 0 24 24" aria-hidden="true"><path d="M2 5h20v14H2z" fill="none"/><path d="M2 5h20v14H2V5zm2 2v.5l8 5 8-5V7H4z"/></svg>
          tessa.brogan@quellmail.com
        </li>
      </ul>
    </div>
    <div class="portrait" role="img" aria-label="Circular portrait photo of the trainer, smiling, with long curly hair"></div>
  </section>
</body>
</html>
```